Venture 482 - Lumora Book Cover

I am looking for a Lumora book cover for my book about "Venture 482".
The Book is Titled:
Venture 482 Ascended
Shaping Outcomes: Paths To Unlocking Cosmic Truths
Author is Dorian Pell
Here is a book description that may help you understand more about it:
Inspired by the genius of Edwin Marlowe, this comprehensive guide delves into the ancient wisdom and cutting-edge science behind the 482 method, a powerful tool for manifesting your desires. Whether you're seeking personal growth, financial success, or spiritual enlightenment, this book provides advanced techniques and methods to transform your dreams into reality.
Any questions please ask.
Thanks
Owen

```html
<!DOCTYPE html>
<html lang="en">
<head>
<meta charset="utf-8">
<title>Venture 482 Ascended — Dorian Pell</title>
<link rel="stylesheet" href="https://fonts.googleapis.com/css2?family=Lexend:wght@700&family=Gloock&family=Cinzel:wght@700&family=Tenor+Sans&family=Tinos&display=swap">
<style>
  :root {
    --page-bg: #e9e9e7;
    --sky-deep: #24324c;
    --sky-mid: #6d8bb3;
    --sky-light: #b7c7d9;
    --horizon: #dfe3e8;
    --ground: #a6a6a8;
    --ground-dark: #8d8f93;
    --title-cream: #fbe9dc;
    --author-blush: #f1cbbb;
    --edition-ivory: #fdf6d6;
    --edition-shadow: #1d2434;
    --subtitle-white: #ffffff;
  }
  * { margin: 0; padding: 0; box-sizing: border-box; }
  html, body {
    width: 1200px;
    height: 1131px;
    overflow: hidden;
    background: var(--page-bg);
  }
  .stage {
    width: 1200px;
    height: 1131px;
    display: flex;
    justify-content: center;
    align-items: center;
  }
  .cover {
    position: relative;
    width: 749px;
    height: 1131px;
    overflow: hidden;
  }
  .cover-art {
    position: absolute;
    inset: 0;
    background: linear-gradient(180deg,
      var(--sky-deep) 0%,
      #3f5678 14%,
      var(--sky-mid) 36%,
      var(--sky-light) 58%,
      var(--horizon) 64.5%,
      var(--ground) 66%,
      var(--ground-dark) 100%);
  }
  .cover-text {
    position: absolute;
    left: 0;
    width: 100%;
    text-align: center;
    white-space: nowrap;
  }
  .author {
    top: 76px;
    font-family: "Tenor Sans", sans-serif;
    font-size: 44px;
    letter-spacing: 0.36em;
    padding-left: 0.36em;
    color: var(--author-blush);
  }
  .title-word {
    top: 166px;
    font-family: "Lexend", sans-serif;
    font-weight: 700;
    font-size: 92px;
    line-height: 1;
    letter-spacing: -0.03em;
    color: var(--title-cream);
    text-shadow: 0 6px 10px rgba(20, 28, 45, 0.45);
  }
  .title-number {
    top: 248px;
    font-family: "Gloock", serif;
    font-size: 256px;
    line-height: 1;
    letter-spacing: -0.04em;
    color: var(--title-cream);
  }
  .edition {
    top: 505px;
    font-family: "Cinzel", serif;
    font-weight: 700;
    font-size: 48px;
    letter-spacing: 0.5em;
    padding-left: 0.5em;
    color: var(--edition-ivory);
    text-shadow: 3px 3px 0 var(--edition-shadow);
  }
  .subtitle-lead {
    top: 972px;
    font-family: "Tenor Sans", sans-serif;
    font-size: 27px;
    letter-spacing: 0.02em;
    color: var(--subtitle-white);
  }
  .subtitle-body {
    top: 1022px;
    font-family: "Tinos", serif;
    font-size: 23px;
    line-height: 1.3;
    color: var(--subtitle-white);
  }
</style>
</head>
<body>
  <main class="stage">
    <article class="cover">
      <div class="cover-art" role="img" aria-label="Cover scene: a man in a dark suit seen from behind stands before a tall glass doorway under a blue cloudy sky, on a silver plain with a mirrored reflecting pool in front of him"></div>
      <p class="cover-text author">DORIAN PELL</p>
      <h1>
        <span class="cover-text title-word">VENTURE</span>
        <span class="cover-text title-number">482</span>
      </h1>
      <p class="cover-text edition">ASCENDED</p>
      <p class="cover-text subtitle-lead">SHAPING OUTCOMES:</p>
      <p class="cover-text subtitle-body">Paths to unlocking<br>cosmic truths</p>
    </article>
  </main>
</body>
</html>
```